Brand new letterhead, business card, email signature etc.

We are a financial company in London, UK. Our website is www.marlowvane.com. We're wanting a complete remodel of the company colours, letter head, business cards, email signatures, etc. Looking to keep the same font for the company name. I have upload a colour palette that we want to work with. We're looking for company letterhead for outgoing letters/ correspondence, letterhead for internal documentation, email signatures, e-letters. etc. Ultimately we will redesign the entire website also. It is important that our clients get a strong, secure, warm, trustworthy, solid feeling and first impression.
Updates

Designs look the same

Target Market(s)

Institutional investors, (ultra) high net worth individuals

Industry/Entity Type

Finance, Invesments banking.

Font styles to use
Other font styles liked:
• Current font is "Champagne & Limousines"

Requirements
Must have
• Must use the colours provided on the PDF uploaded to the portal. The purple = main colour. The red = accent colour.
Nice to have
• Nice to use same font as now for the company name "Corvane". Font is "Champagne & Limousines". Nice to have some reference to the old logo flower, but only subtle.
Should not have
• Do not use the colour red from our website. Use the colours provided on the colour palette PDF that I uploaded in the portal.

```html
<!DOCTYPE html>
<html lang="en">
<head>
<meta charset="utf-8">
<title>Corvane Stationery</title>
<link rel="stylesheet" href="https://fonts.googleapis.com/css2?family=Josefin+Sans:wght@300&family=Montserrat:wght@400;500;600&family=Great+Vibes&display=swap">
<style>
  :root {
    --plum: #2e0019;
    --accent: #c8321a;
    --paper: #e6e6e6;
    --ink: #1c1c1c;
    --backdrop: #d4d4d4;
  }
  * { margin: 0; padding: 0; box-sizing: border-box; }
  html, body { width: 1200px; height: 971px; overflow: hidden; }
  body {
    background: var(--backdrop);
    font-family: "Montserrat", sans-serif;
    color: var(--ink);
    position: relative;
  }
  .piece { position: absolute; overflow: hidden; }
  .footer-band { position: absolute; left: 0; bottom: 0; display: block; }
  .footer-url {
    position: absolute; color: #fff; font-size: 13.5px; letter-spacing: 0.2px; white-space: nowrap;
  }
  .wordmark {
    font-family: "Josefin Sans", sans-serif; font-weight: 300;
    text-transform: uppercase; letter-spacing: 0.14em; line-height: 1;
    position: absolute; white-space: nowrap;
  }
  .mark-square { position: absolute; border: 1px solid #555; }
  .icon { width: 7px; height: 7px; vertical-align: -1px; margin-right: 3px; }

  /* Folder */
  .folder { left: 49px; top: 232px; width: 502px; height: 647px; background: var(--plum); }

  /* Letterhead */
  .letterhead { left: 131px; top: 32px; width: 505px; height: 685px; background: var(--paper); }
  .letterhead .mark-square { left: 35px; top: 41px; width: 49px; height: 49px; }
  .letterhead .wordmark { left: 95px; top: 52px; font-size: 30px; color: #222; }
  .sender-block { position: absolute; left: 372px; top: 25px; font-size: 9.5px; line-height: 12.3px; font-style: normal; }
  .sender-block .contact { margin-top: 3px; font-size: 8px; line-height: 10.5px; }
  .letter-body { position: absolute; left: 34px; top: 174px; width: 437px; font-size: 9.5px; line-height: 10.8px; }
  .letter-body p { margin-bottom: 10.5px; text-align: justify; }
  .letter-body .date { margin-bottom: 12px; }
  .letter-body .recipient { margin-bottom: 12px; text-align: left; }
  .letter-body .salutation { font-size: 11.5px; font-weight: 600; margin-bottom: 13px; }
  .letter-body .signoff { margin-top: 20px; }
  .signature { font-family: "Great Vibes", cursive; font-size: 22px; margin-top: 10px; }
  .letterhead .footer-url { left: 321px; bottom: 9px; }

  /* Business card front */
  .card-front { left: 665px; top: 51px; width: 243px; height: 138px; background: var(--paper); border-radius: 12px; }
  .card-front .mark-square { left: 34px; top: 34px; width: 70px; height: 70px; }
  .card-front .divider { position: absolute; left: 120px; top: 32px; width: 1px; height: 75px; background: var(--accent); }
  .card-details { position: absolute; left: 129px; top: 31px; font-size: 5.6px; line-height: 8.3px; white-space: nowrap; }
  .card-details .person { font-size: 8px; font-weight: 600; line-height: 10px; }
  .card-details .person .given { color: var(--accent); }
  .card-details .person .family { color: var(--plum); }
  .card-details .role { margin-bottom: 5px; }
  .card-details .street { margin-bottom: 4px; }
  .card-details .icon { width: 5px; height: 5px; margin-right: 2px; vertical-align: 0; }
  .card-front .footer-url { font-size: 6.5px; left: 154px; bottom: 4px; }

  /* Business card back */
  .card-back { left: 916px; top: 51px; width: 243px; height: 138px; background: var(--plum); border-radius: 12px; }
  .card-back .mark-square { left: 39px; top: 49px; width: 40px; height: 40px; border-color: #d9cbd3; }
  .card-back .wordmark { left: 89px; top: 58px; font-size: 22px; color: #fff; }

  /* Email signature */
  .email-signature { left: 667px; top: 206px; width: 490px; height: 115px; background: var(--paper); }
  .email-signature .mark-square { left: 19px; top: 30px; width: 30px; height: 30px; }
  .email-signature .wordmark { left: 57px; top: 39px; font-size: 15.5px; letter-spacing: 0.12em; color: #333; }
  .email-signature .divider { position: absolute; width: 1px; height: 46px; top: 22px; background: var(--plum); }
  .sig-person { position: absolute; right: 187px; top: 22px; text-align: right; font-size: 11px; line-height: 16px; white-space: nowrap; }
  .sig-person .name { font-size: 12px; font-weight: 600; }
  .sig-person .name .given { color: var(--accent); }
  .sig-person .name .family { color: var(--plum); }
  .sig-contacts { position: absolute; left: 330px; top: 21px; font-size: 11px; line-height: 17px; white-space: nowrap; }
  .sig-contacts .icon { width: 9px; height: 9px; margin-right: 6px; }
  .email-signature .footer-url { left: 322px; bottom: 7px; font-size: 12.5px; }

  /* Compliment slip */
  .compliment-slip { left: 661px; top: 349px; width: 488px; height: 243px; background: var(--paper); }
  .compliment-slip .mark-square { left: 18px; top: 23px; width: 26px; height: 26px; }
  .compliment-slip .wordmark { left: 50px; top: 30px; font-size: 14.5px; color: #333; }
  .slip-address { position: absolute; left: 18px; top: 150px; font-size: 7.3px; line-height: 10px; font-style: normal; }
  .slip-address .contact { margin-top: 5px; }
  .slip-address .icon { width: 6px; height: 6px; }
  .compliment-slip .footer-url { left: 319px; bottom: 9px; }

  /* Envelope */
  .envelope { left: 662px; top: 632px; width: 487px; height: 244px; }
</style>
</head>
<body>

  <div class="piece folder"></div>

  <article class="piece letterhead">
    <div class="mark-square"></div>
    <div class="wordmark">Corvane</div>
    <address class="sender-block">
      Corvane Group Limited<br>4th Floor<br>18 Harrow Yard<br>London<br>EC3N 2LT
      <div class="contact">
        <svg class="icon" viewBox="0 0 10 10"><path d="M2 1 L4 1 L4.6 3.2 L3.4 4 Q4.4 6 6 6.6 L6.8 5.4 L9 6 L9 8 Q5 9 1 2 Z" fill="#333"/></svg>020-555-0147<br>
        <svg class="icon" viewBox="0 0 10 10"><rect x="1" y="2" width="8" height="6" fill="#333"/><path d="M1 2 L5 5.5 L9 2" stroke="#e6e6e6" fill="none"/></svg>info@marlowvane.com
      </div>
    </address>
    <div class="letter-body">
      <p class="date">January-03-2020</p>
      <p class="recipient">Mr, Daniel Ashby<br>President</p>
      <p class="recipient">Harlow Tern Ltd<br>48 Ledger Street, Suite# 12<br>Bristol, BS1 4QA</p>
      <p class="salutation">Dear Mr, Ashby</p>
      <p>Lorem ipsum dolor sit amet, consectetur adipisicing elit, sed do eiusmod tempor incididunt ut labore et dolore magna aliqua. Ut enim ad minim veniam, quis nostrud exercitation ullamco laboris nisi ut aliquip ex ea commodo consequat. Duis aute irure dolor in reprehenderit in voluptate velit esse cillum dolore eu fugiat nulla pariatur.</p>
      <p>Lorem ipsum dolor sit amet, consectetur adipisicing elit, sed do eiusmod tempor incididunt ut labore et dolore magna aliqua. Ut enim ad minim veniam, quis nostrud exercitation ullamco laboris nisi ut aliquip ex ea commodo consequat. Duis aute irure dolor in reprehenderit in voluptate velit esse cillum dolore eu fugiat nulla pariatur.</p>
      <p>Lorem ipsum dolor sit amet, consectetur adipisicing elit, sed do eiusmod tempor incididunt ut labore et dolore magna aliqua. Ut enim ad minim veniam, quis nostrud exercitation ullamco laboris nisi ut aliquip ex ea commodo consequat.</p>
      <p>Excepteur sint occaecat cupidatat non proident, sunt in culpa qui officia deserunt mollit anim id est laborum. re et dolore magnam aliquam quaerat voluptatem.</p>
      <p class="signoff">Regards</p>
      <p class="signature">Thomas Reyne</p>
    </div>
    <svg class="footer-band" width="505" height="32" viewBox="0 0 505 32">
      <polygon points="292,0 505,0 505,32 262,32" fill="var(--plum)"/>
      <polygon points="0,7 285,7 281,11 0,11" fill="var(--plum)"/>
      <polygon points="0,15 274,15 258,32 0,32" fill="var(--accent)"/>
    </svg>
    <span class="footer-url">www.marlowvane.com</span>
  </article>

  <section class="piece card-front">
    <div class="mark-square"></div>
    <div class="divider"></div>
    <div class="card-details">
      <div class="person"><span class="given">ELISE</span> <span class="family">MARWOOD</span></div>
      <div class="role">Managing Director</div>
      <div class="street">6 Fenwick Lane<br>Suite 3B London EC2M 4PT</div>
      <div>
        <svg class="icon" viewBox="0 0 10 10"><path d="M2 1 L4 1 L4.6 3.2 L3.4 4 Q4.4 6 6 6.6 L6.8 5.4 L9 6 L9 8 Q5 9 1 2 Z" fill="#333"/></svg>020-555-0192<br>
        <svg class="icon" viewBox="0 0 10 10"><rect x="1" y="2" width="8" height="6" fill="#333"/><path d="M1 2 L5 5.5 L9 2" stroke="#e6e6e6" fill="none"/></svg>em@marlowvane.com<br>
        <svg class="icon" viewBox="0 0 10 10"><circle cx="5" cy="5" r="4" fill="#333"/><path d="M1 5 H9 M5 1 V9" stroke="#e6e6e6" stroke-width="0.8"/></svg>www.marlowvane.com
      </div>
    </div>
    <svg class="footer-band" width="243" height="16" viewBox="0 0 243 16">
      <polygon points="140,0 243,0 243,16 126,16" fill="var(--plum)"/>
      <polygon points="0,4 134,4 132,6 0,6" fill="var(--plum)"/>
      <polygon points="0,9 130,9 123,16 0,16" fill="var(--accent)"/>
    </svg>
    <span class="footer-url">www.marlowvane.com</span>
  </section>

  <section class="piece card-back">
    <div class="mark-square"></div>
    <div class="wordmark">Corvane</div>
  </section>

  <section class="piece email-signature">
    <div class="mark-square"></div>
    <div class="wordmark">Corvane</div>
    <div class="divider" style="left:161px"></div>
    <div class="sig-person">
      <div class="name"><span class="given">ELISE</span> <span class="family">MARWOOD</span></div>
      <div>Managing Director</div>
      <div>Suite 3B London EC2M</div>
    </div>
    <div class="divider" style="left:316px"></div>
    <div class="sig-contacts">
      <div><svg class="icon" viewBox="0 0 10 10"><path d="M2 1 L4 1 L4.6 3.2 L3.4 4 Q4.4 6 6 6.6 L6.8 5.4 L9 6 L9 8 Q5 9 1 2 Z" fill="var(--plum)"/></svg>020-555-0192</div>
      <div><svg class="icon" viewBox="0 0 10 10"><rect x="1" y="2" width="8" height="6" fill="var(--plum)"/><path d="M1 2 L5 5.5 L9 2" stroke="#e6e6e6" fill="none"/></svg>em@marlowvane.com</div>
      <div><svg class="icon" viewBox="0 0 10 10"><circle cx="5" cy="5" r="4" fill="var(--plum)"/><path d="M1 5 H9 M5 1 V9" stroke="#e6e6e6" stroke-width="0.8"/></svg>www.marlowvane.com</div>
    </div>
    <svg class="footer-band" width="490" height="30" viewBox="0 0 490 30">
      <polygon points="283,0 490,0 490,30 252,30" fill="var(--plum)"/>
      <polygon points="0,7 276,7 272,11 0,11" fill="var(--plum)"/>
      <polygon points="0,14 268,14 253,30 0,30" fill="var(--accent)"/>
    </svg>
    <span class="footer-url">www.marlowvane.com</span>
  </section>

  <section class="piece compliment-slip">
    <div class="mark-square"></div>
    <div class="wordmark">Corvane</div>
    <address class="slip-address">
      Corvane Group Limited<br>4th Floor, 18 Harrow Yard<br>London EC3N 2LT
      <div class="contact">
        <svg class="icon" viewBox="0 0 10 10"><path d="M2 1 L4 1 L4.6 3.2 L3.4 4 Q4.4 6 6 6.6 L6.8 5.4 L9 6 L9 8 Q5 9 1 2 Z" fill="#333"/></svg>020-555-0147<br>
        <svg class="icon" viewBox="0 0 10 10"><rect x="1" y="2" width="8" height="6" fill="#333"/><path d="M1 2 L5 5.5 L9 2" stroke="#e6e6e6" fill="none"/></svg>info@marlowvane.com
      </div>
    </address>
    <svg class="footer-band" width="488" height="31" viewBox="0 0 488 31">
      <polygon points="282,0 488,0 488,31 256,31" fill="var(--plum)"/>
      <polygon points="0,6 274,6 270,11 0,11" fill="var(--plum)"/>
      <polygon points="0,15 268,15 254,31 0,31" fill="var(--accent)"/>
    </svg>
    <span class="footer-url">www.marlowvane.com</span>
  </section>

  <svg class="piece envelope" width="487" height="244" viewBox="0 0 487 244" role="img" aria-label="Envelope back with plum flap">
    <rect x="0" y="0" width="487" height="244" fill="var(--paper)"/>
    <path d="M12 40 L14 240 M475 40 L473 240" stroke="#cfcfcf" stroke-width="1" fill="none"/>
    <path d="M0 0 H487 Q480 45 455 48 L243 78 L32 48 Q8 45 0 0 Z" fill="var(--plum)"/>
  </svg>

</body>
</html>
```